Keystone Trench Co Business Card*

Looking for a professional, clean and crisp business card

I am in the underground utilities industry and am just looking for a really impressive business card. I would like our card to be white with our symbol crisp and clear with it protruding. I also have a business partner that will require his name and info on the card once the design is set. I would like to have our website info on the card which is;
http://keystonetrenchco.example/

Contact Information for Business Card

Website, contact name, number and email

```html
<!DOCTYPE html>
<html lang="en">
<head>
<meta charset="utf-8">
<title>Keystone Trench Co — Business Card</title>
<link href="https://fonts.googleapis.com/css2?family=Teko:wght@600&family=Quicksand:wght@500&display=swap" rel="stylesheet">
<style>
  :root {
    --page: #e9ebee;
    --card-white: #ffffff;
    --brand-blue: #3a5fa8;
    --slate: #2c3440;
    --ink: #2a2d33;
    --back-dark: #0c0e11;
    --back-mid: #1b1f25;
    --logo-white: #ffffff;
  }
  * { margin: 0; padding: 0; box-sizing: border-box; }
  html, body { width: 1200px; height: 900px; overflow: hidden; }
  body { background: var(--page); position: relative; font-family: "Quicksand", sans-serif; }

  .card {
    position: absolute;
    left: 270px;
    width: 660px;
    height: 377px;
    overflow: hidden;
    box-shadow: 0 10px 28px rgba(0,0,0,.18);
  }
  .card--back { top: 53px; }
  .card--front { top: 470px; background: var(--card-white); }

  /* back side */
  .back-texture {
    position: absolute; inset: 0;
    background: linear-gradient(135deg, var(--back-mid) 0%, var(--back-dark) 55%, var(--back-mid) 100%);
  }
  .back-logo {
    position: absolute;
    right: 40px; top: 150px;
    display: flex; align-items: center; gap: 12px;
  }
  .back-logo__dot {
    width: 22px; height: 22px; border-radius: 50%;
    background: var(--logo-white);
  }
  .back-logo__name {
    font-family: "Teko", sans-serif;
    font-weight: 600;
    font-size: 40px;
    line-height: 1;
    color: var(--logo-white);
    letter-spacing: 1px;
    text-transform: uppercase;
  }

  /* front side */
  .band { position: absolute; }
  .band--top-slate { top: 0; left: 330px; right: 0; height: 8px; background: var(--slate); }
  .band--top-blue { top: 8px; left: 378px; right: 0; height: 22px; background: var(--brand-blue); }
  .band--bottom-blue { bottom: 8px; left: 0; width: 300px; height: 24px; background: var(--brand-blue); }
  .band--bottom-slate { bottom: 0; left: 0; right: 0; height: 8px; background: var(--slate); }

  .holder-name {
    position: absolute;
    left: 36px; top: 158px;
    width: 290px;
    white-space: nowrap;
    font-family: "Teko", sans-serif;
    font-weight: 600;
    font-size: 46px;
    line-height: 1;
    color: var(--brand-blue);
    letter-spacing: 1px;
    text-transform: uppercase;
  }
  .divider {
    position: absolute;
    left: 340px; top: 150px;
    width: 2px; height: 76px;
    background: var(--brand-blue);
  }
  .contact-list {
    position: absolute;
    left: 356px; top: 150px;
    list-style: none;
  }
  .contact-list li {
    display: flex; align-items: center; gap: 9px;
    font-size: 16px;
    line-height: 25px;
    color: var(--ink);
    white-space: nowrap;
  }
  .contact-list svg { width: 17px; height: 17px; flex: none; }
  .accent { color: var(--brand-blue); }
</style>
</head>
<body>

  <section class="card card--back" aria-label="Card back">
    <div class="back-texture" role="img" aria-label="Dark diagonal pattern of pipe sections"></div>
    <div class="back-logo">
      <span class="back-logo__dot"></span>
      <span class="back-logo__name">Keystone Trench Co</span>
    </div>
  </section>

  <section class="card card--front" aria-label="Card front">
    <div class="band band--top-slate"></div>
    <div class="band band--top-blue"></div>
    <div class="band band--bottom-blue"></div>
    <div class="band band--bottom-slate"></div>

    <h1 class="holder-name">Dale Hartwick</h1>
    <div class="divider"></div>

    <ul class="contact-list">
      <li>
        <svg viewBox="0 0 24 24" fill="none" stroke="#3a5fa8" stroke-width="1.8"><circle cx="12" cy="12" r="10"/><path d="M8.5 7.5c.6-.6 1.4-.4 1.7.3l.6 1.4c.2.5 0 1-.4 1.3l-.6.4c.6 1.4 1.6 2.4 3 3l.4-.6c.3-.4.8-.6 1.3-.4l1.4.6c.7.3.9 1.1.3 1.7-1 1-2.6 1.2-4.6-.2-1.4-1-2.6-2.2-3.5-3.6-1.2-1.9-1-3.4 0-4.2z"/></svg>
        604-555-0182
      </li>
      <li>
        <svg viewBox="0 0 24 24" fill="none" stroke="#3a5fa8" stroke-width="1.8"><rect x="2.5" y="5" width="19" height="14" rx="1"/><path d="M3 6l9 7 9-7"/></svg>
        dale@keystonetrenchco.example
      </li>
      <li>
        <svg viewBox="0 0 24 24" fill="none" stroke="#3a5fa8" stroke-width="1.8"><circle cx="12" cy="12" r="9.5"/><path d="M2.5 12h19M12 2.5c3 3 3 16 0 19M12 2.5c-3 3-3 16 0 19"/></svg>
        <span>www.<span class="accent">keystonetrenchco</span>.example</span>
      </li>
    </ul>
  </section>

</body>
</html>
```